Relaydeck Tech Company Website B2B Dev Teams Corvanix

We need a completely new website for this tech company. We offer software as a service to companies that have private Corvanix software. Our clients are developers, tech teams, and companies (B2B). We offer a way to keep Corvanix devices updated worldwide without needing a Vantora Shelf account, which suits corporate-owned single-use devices very well.
Our public is technicians (software developers), not people who use smartphones. Most clients run Relaydeck on tablets, drones, point-of-sale devices, etc.
The most used feature is the background update, which requires no user interaction. Our product helps developers keep their private enterprise applications updated. Some references of what developers like to see:
mivorin.example, taskobri.example, flowquenta.example, dravelo.example, kondrix.example
The green doesn't suit it very well. Feel free to change the logo's color (source images .ai .psd attached). The current website has only five small pages. The new one can have five at most (it can have less). The images of the "update strategies" aren't good. It can be replaced by "mock-like" images mimicking how Corvanix interacts with the user. The proportion of the tool icons isn't good. The login and signup forms can be improved a lot.
We hope for a modern website for a tech company with new colors that, at first glance, convey a sense of quality. We want the current standard for SaaS (software as a service) providers' websites.
https://www.relaydeck-app.example/
NO WORDPRESS.
We want it built using Next, Nuxt, or another good static build tool.

Target Market(s)
Corvanix Software Development
Industry/Entity Type
Software
Coding
Coded - Design and coding required
Number of Pages Required
4 page
Requirements
Must have
- We want it built using Next, Nuxt, or another good static build tool

Nice to have
- Corvanix message notification mockups instead screenshots

Should not have
- wordpress

```html
<!DOCTYPE html>
<html lang="en">
<head>
<meta charset="utf-8">
<title>Relaydeck – Register</title>
<link href="https://fonts.googleapis.com/css2?family=Poppins:wght@400;500;600;700&family=Roboto:wght@400;500&display=swap" rel="stylesheet">
<style>
  :root {
    --page-bg: #f2f2f2;
    --navy: #0a0a5c;
    --navy-deep: #07074f;
    --blue: #0b4a8f;
    --link: #1b3fa8;
    --ink: #111111;
    --text: #1e1e1e;
    --field: #f3f3f3;
    --crumb-bg: #dfe9f0;
    --card: #ffffff;
    --line: #d6d6de;
  }
  * { box-sizing: border-box; margin: 0; padding: 0; }
  html, body { width: 1100px; height: 1200px; overflow: hidden; }
  body { background: var(--page-bg); font-family: "Poppins", sans-serif; color: var(--text); position: relative; }
  a { color: inherit; text-decoration: none; }
  .abs { position: absolute; }

  .brand { font-family: "Poppins", sans-serif; font-weight: 700; color: var(--navy); letter-spacing: -0.5px; }
  .site-header .brand { left: 34px; top: 26px; font-size: 27px; line-height: 36px; }

  .main-nav { left: 374px; top: 27px; width: 359px; height: 35px; background: #ececec; border-radius: 18px;
    display: flex; align-items: center; justify-content: space-around; padding: 0 12px; font-size: 11.5px; color: var(--ink); }

  .btn { display: flex; align-items: center; justify-content: center; gap: 6px; border-radius: 20px;
    font-size: 10.5px; font-weight: 600; text-transform: uppercase; }
  .btn-outline { border: 1.5px solid var(--navy); color: var(--navy); background: transparent; }
  .btn-solid { background: var(--navy); color: #fff; }
  .btn-gradient { background: linear-gradient(90deg, #0d5aa6, #071f6b); color: #fff; }
  .site-header .btn-login { left: 879px; top: 25px; width: 89px; height: 38px; }
  .site-header .btn-signup { left: 979px; top: 25px; width: 89px; height: 38px; }

  .breadcrumb { left: 0; top: 80px; width: 1100px; height: 39px; background: var(--crumb-bg);
    display: flex; align-items: center; padding-left: 34px; font-size: 11px; gap: 9px; }
  .breadcrumb .current { color: var(--blue); font-weight: 600; }

  .page-title { left: 0; width: 1100px; top: 180px; text-align: center; font-size: 27px; font-weight: 600; color: var(--ink); }

  .register-card { left: 259px; top: 256px; width: 614px; height: 469px; background: var(--card);
    border: 1px solid #e2e2e2; border-radius: 20px; }
  .field { left: 32px; width: 550px; height: 36px; background: var(--field); border-radius: 6px;
    display: flex; align-items: center; padding-left: 20px; font-size: 11px; color: var(--ink); }
  .have-account { left: 32px; top: 243px; font-size: 9px; color: var(--ink); }
  .have-account a { color: var(--navy); font-weight: 600; text-decoration: underline; }
  .check-row { left: 32px; font-size: 9px; color: var(--ink); display: flex; align-items: center; gap: 6px; white-space: nowrap; }
  .check-row .box { width: 8px; height: 8px; border: 1px solid #555; border-radius: 1.5px; flex: none; }
  .check-row a { color: var(--link); text-decoration: underline; }

  .human-check { left: 206px; top: 328px; width: 202px; height: 47px; background: #f9f9f9;
    border: 1px solid #d3d3d3; border-radius: 3px; font-family: "Roboto", sans-serif; }
  .human-check .tick { left: 9px; top: 12px; width: 22px; height: 22px; border: 2px solid #c1c1c1; border-radius: 2px; background: #fff; }
  .human-check .label { left: 39px; top: 15px; font-size: 11px; color: #222; }
  .human-check .mark { left: 163px; top: 7px; width: 18px; height: 18px; border-radius: 50%; background: #9bb3e0; }
  .human-check .name { right: 8px; top: 29px; font-size: 5.5px; color: #666; }
  .human-check .legal { right: 7px; top: 38px; font-size: 4.5px; color: #888; }

  .btn-register { left: 248px; top: 398px; width: 119px; height: 38px; border: 1px solid var(--ink);
    color: var(--ink); font-size: 10.5px; border-radius: 20px; background: transparent; font-family: inherit; }

  .footer-rule { left: 0; top: 811px; width: 1100px; height: 1px; background: var(--line); }
  .site-footer .brand { left: 129px; top: 899px; font-size: 33px; line-height: 44px; }
  .tagline { left: 129px; top: 972px; width: 270px; font-size: 12px; line-height: 19.5px; color: var(--ink); }
  .site-footer .btn-login { left: 129px; top: 1045px; width: 89px; height: 38px; }
  .site-footer .btn-signup { left: 229px; top: 1045px; width: 89px; height: 38px; }

  .footer-col h3 { font-size: 17px; font-weight: 500; color: #14144a; margin-bottom: 14px; }
  .footer-col ul { list-style: none; }
  .footer-col li { display: flex; align-items: center; gap: 12px; height: 33.6px; font-size: 14.5px; color: #2a2a2a; }
  .footer-col li svg { flex: none; margin-left: 3px; }
  .col-quick { left: 446px; top: 893px; }
  .col-features { left: 606px; top: 893px; }
  .col-other { left: 804px; top: 893px; }

  .to-top { left: 1046px; top: 1082px; width: 26px; height: 26px; background: #e3e3e3; border-radius: 4px;
    display: flex; align-items: center; justify-content: center; }

  .bottom-bar { left: 0; top: 1153px; width: 1100px; height: 47px; background: var(--navy-deep); }
  .social { top: 11px; width: 26px; height: 26px; border-radius: 50%; border: 1px solid #ffffff; }
  .social.active { background: #ffffff; }
</style>
</head>
<body>

<header class="site-header">
  <a class="brand abs" href="#">Relaydeck</a>
  <nav class="main-nav abs">
    <a href="#">HOME</a><a href="#">FEATURES</a><a href="#">PRICING</a><a href="#">DOCS</a><a href="#">STATUS</a>
  </nav>
  <a class="btn btn-outline btn-login abs" href="#">
    <svg width="14" height="14" viewBox="0 0 24 24" fill="none" stroke="currentColor" stroke-width="1.8"><path d="M9 4h9v16H9M3 12h11M11 8l4 4-4 4"/></svg>Login</a>
  <a class="btn btn-gradient btn-signup abs" href="#">Sign up</a>
</header>

<div class="breadcrumb abs"><span>Home</span><span>»</span><span class="current">Register</span></div>

<h1 class="page-title abs">Register</h1>

<form class="register-card abs">
  <div class="field abs" style="top:31px">Enter Your Full Name*</div>
  <div class="field abs" style="top:86px">Enter Your Email Address*</div>
  <div class="field abs" style="top:141px">Password*</div>
  <div class="field abs" style="top:196px">Password Confirmation*</div>
  <p class="have-account abs">Already Have Account? <a href="#">Login</a></p>
  <label class="check-row abs" style="top:272px"><span class="box"></span><span>I accept the <a href="#">Terms and Conditions</a>, <a href="#">Privacy Policy</a> and <a href="#" style="color:var(--navy)">Cookies Policy</a></span></label>
  <label class="check-row abs" style="top:294px"><span class="box"></span><span>I want to receive the Relaydeck News and Software Updates</span></label>
  <div class="human-check abs">
    <span class="tick abs"></span>
    <span class="label abs">I'm not a robot</span>
    <span class="mark abs"></span>
    <span class="name abs">VerifyGate</span>
    <span class="legal abs">Privacy · Terms</span>
  </div>
  <button type="button" class="btn btn-register abs">Register</button>
</form>

<div class="footer-rule abs"></div>

<footer class="site-footer">
  <a class="brand abs" href="#">Relaydeck</a>
  <p class="tagline abs">Keep your private Corvanix application self-updated without any third-party process.</p>
  <a class="btn btn-outline btn-login abs" href="#">
    <svg width="14" height="14" viewBox="0 0 24 24" fill="none" stroke="currentColor" stroke-width="1.8"><path d="M9 4h9v16H9M3 12h11M11 8l4 4-4 4"/></svg>Login</a>
  <a class="btn btn-solid btn-signup abs" href="#">Sign up</a>

  <div class="footer-col col-quick abs">
    <h3>Quick Links</h3>
    <ul>
      <li><svg width="8" height="10" viewBox="0 0 8 10"><path d="M2 1l4 4-4 4" fill="none" stroke="#222" stroke-width="1.4"/></svg>Home</li>
      <li><svg width="8" height="10" viewBox="0 0 8 10"><path d="M2 1l4 4-4 4" fill="none" stroke="#222" stroke-width="1.4"/></svg>Features</li>
      <li><svg width="8" height="10" viewBox="0 0 8 10"><path d="M2 1l4 4-4 4" fill="none" stroke="#222" stroke-width="1.4"/></svg>Pricing</li>
      <li><svg width="8" height="10" viewBox="0 0 8 10"><path d="M2 1l4 4-4 4" fill="none" stroke="#222" stroke-width="1.4"/></svg>Docs</li>
      <li><svg width="8" height="10" viewBox="0 0 8 10"><path d="M2 1l4 4-4 4" fill="none" stroke="#222" stroke-width="1.4"/></svg>Status</li>
    </ul>
  </div>
  <div class="footer-col col-features abs">
    <h3>Our Features</h3>
    <ul>
      <li><svg width="8" height="10" viewBox="0 0 8 10"><path d="M2 1l4 4-4 4" fill="none" stroke="#222" stroke-width="1.4"/></svg>Host your apk</li>
      <li><svg width="8" height="10" viewBox="0 0 8 10"><path d="M2 1l4 4-4 4" fill="none" stroke="#222" stroke-width="1.4"/></svg>Devices Enrollment</li>
      <li><svg width="8" height="10" viewBox="0 0 8 10"><path d="M2 1l4 4-4 4" fill="none" stroke="#222" stroke-width="1.4"/></svg>Manage Versions</li>
      <li><svg width="8" height="10" viewBox="0 0 8 10"><path d="M2 1l4 4-4 4" fill="none" stroke="#222" stroke-width="1.4"/></svg>Track Installations</li>
      <li><svg width="8" height="10" viewBox="0 0 8 10"><path d="M2 1l4 4-4 4" fill="none" stroke="#222" stroke-width="1.4"/></svg>View All</li>
    </ul>
  </div>
  <div class="footer-col col-other abs">
    <h3>Other Links</h3>
    <ul>
      <li><svg width="8" height="10" viewBox="0 0 8 10"><path d="M2 1l4 4-4 4" fill="none" stroke="#222" stroke-width="1.4"/></svg>Terms &amp; Conditions</li>
      <li><svg width="8" height="10" viewBox="0 0 8 10"><path d="M2 1l4 4-4 4" fill="none" stroke="#222" stroke-width="1.4"/></svg>Privacy Policy</li>
      <li><svg width="8" height="10" viewBox="0 0 8 10"><path d="M2 1l4 4-4 4" fill="none" stroke="#222" stroke-width="1.4"/></svg>Sitemap</li>
      <li><svg width="8" height="10" viewBox="0 0 8 10"><path d="M2 1l4 4-4 4" fill="none" stroke="#222" stroke-width="1.4"/></svg>Contact Us</li>
    </ul>
  </div>

  <a class="to-top abs" href="#" aria-label="Back to top">
    <svg width="10" height="12" viewBox="0 0 10 12"><path d="M5 11V1M1 5l4-4 4 4" fill="none" stroke="#333" stroke-width="1.2"/></svg>
  </a>

  <div class="bottom-bar abs">
    <span class="social abs" style="left:839px" aria-label="Social profile"></span>
    <span class="social active abs" style="left:874px" aria-label="Social profile"></span>
    <span class="social abs" style="left:909px" aria-label="Social profile"></span>
    <span class="social abs" style="left:943px" aria-label="Social profile"></span>
  </div>
</footer>

</body>
</html>
```